Corvin Ridge Software PowerPoint template

We are a software company selling endpoint visibility, access and security technology to enterprise-level IT departments.
Our technology helps organizations gain comprehensive visibility into and control over devices accessing their corporate network so they can quickly identify and address suspicious activity on the network that could lead to potential threats like data breaches.
This technology can cost organizations upwards of $1M - depending on the size of the organization. Our primary clients are Vestral 2,000 companies.
We want a professional, polished PowerPoint template that we can use for all company presentations. Please include:
Title page
Section page
General info page
Thank you page
Logo options and color specs are attached.
Please include our tagline on at least the title page: Discover the edge. Optimize the whole.
Reason: Seeking more options. Looking for a clean design that uses lots of white space.
Software

```html
<!DOCTYPE html>
<html lang="en">
<head>
<meta charset="utf-8">
<title>Corvin Ridge Software – Presentation Template</title>
<link href="https://fonts.googleapis.com/css2?family=Open+Sans:wght@400;600;700&display=swap" rel="stylesheet">
<style>
  :root {
    --stage: #231f20;
    --paper: #ffffff;
    --brand-red: #8b1d1f;
    --brand-copper: #d3826a;
    --brand-gold: #e9b422;
    --mist: #e6e6ea;
    --ink: #111111;
    --ink-soft: #333333;
    --muted: #8a8a8a;
  }
  * { box-sizing: border-box; margin: 0; padding: 0; }
  html, body { width: 1200px; height: 924px; overflow: hidden; }
  body {
    background: var(--stage);
    font-family: "Open Sans", Arial, sans-serif;
    color: var(--ink);
    position: relative;
  }
  .slide {
    position: absolute;
    width: 557px;
    height: 417px;
    background: var(--paper);
    overflow: hidden;
  }
  .slide--title   { left: 26px;  top: 26px; }
  .slide--section { left: 613px; top: 26px; }
  .slide--info    { left: 26px;  top: 476px; height: 421px; }
  .slide--thanks  { left: 613px; top: 476px; height: 421px; }

  .chrome { position: absolute; inset: 0; width: 100%; height: 100%; }

  .brand-mark {
    position: absolute;
    right: 28px;
    top: 19px;
    display: flex;
    align-items: center;
    gap: 6px;
    color: var(--brand-red);
    font-weight: 700;
    font-size: 9.5px;
    letter-spacing: 1.2px;
    line-height: 1.1;
    text-transform: uppercase;
  }
  .brand-mark__square { width: 8px; height: 8px; background: var(--brand-copper); }

  .footer-url {
    position: absolute;
    left: 80px;
    bottom: 14px;
    font-size: 14px;
    color: var(--ink-soft);
  }

  /* Title slide */
  .hero-brand {
    position: absolute;
    left: 186px;
    top: 160px;
    color: var(--brand-red);
    font-weight: 700;
    font-size: 40px;
    letter-spacing: 4px;
    line-height: 1.1;
  }
  .hero-brand span { display: block; font-size: 22px; letter-spacing: 11px; }
  .hero-square {
    position: absolute; left: 140px; top: 178px;
    width: 28px; height: 28px; background: var(--brand-copper);
  }
  .tagline {
    position: absolute; left: 188px; top: 236px;
    font-size: 12px; color: var(--muted); letter-spacing: 0.3px;
  }
  .deck-title {
    position: absolute; right: 12px; top: 315px;
    font-size: 26px; font-weight: 400; color: var(--ink); text-align: right;
  }
  .deck-desc {
    position: absolute; right: 12px; top: 350px;
    font-size: 19px; color: var(--muted); text-align: right;
  }

  /* Headings */
  .page-heading {
    position: absolute; left: 20px; top: 38px;
    font-size: 18px; font-weight: 400; color: var(--ink-soft);
    letter-spacing: 0.2px;
  }
  .page-heading strong { color: var(--brand-red); font-weight: 700; }
  .page-subheading {
    position: absolute; left: 25px; top: 64px;
    font-size: 12px; color: var(--muted);
  }

  /* Section slide */
  .lead {
    position: absolute; left: 40px; top: 96px; width: 480px;
    font-size: 9px; line-height: 1.45; text-align: center; color: var(--ink);
  }
  .checklist { position: absolute; list-style: none; font-size: 8px; line-height: 1.45; color: var(--ink); }
  .checklist--left  { left: 24px;  top: 152px; width: 180px; }
  .checklist--right { left: 215px; top: 152px; width: 160px; }
  .checklist li { margin-bottom: 14px; }
  .checklist--right li + li { margin-top: 34px; }
  .checklist h4 { font-size: 8.5px; font-weight: 700; margin-bottom: 3px; display: flex; align-items: center; gap: 10px; }
  .checklist h4::before { content: ""; width: 7px; height: 7px; border: 1px solid var(--ink); }
  .icon-ring { position: absolute; left: 380px; top: 135px; width: 177px; height: 200px; }

  /* Info slide */
  .chart { position: absolute; left: 14px; top: 100px; width: 260px; height: 130px; }
  .chart-heading {
    position: absolute; left: 30px; top: 252px; width: 218px;
    font-size: 9px; line-height: 1.45; color: var(--ink);
  }
  .chart-heading strong { display: block; font-size: 9.5px; }
  .legend-list { position: absolute; left: 314px; top: 72px; width: 190px; list-style: none; font-size: 8px; line-height: 1.45; }
  .legend-list li { margin-bottom: 14px; }
  .legend-list h4 { font-size: 9px; font-weight: 700; display: flex; align-items: center; gap: 12px; margin-bottom: 3px; }
  .legend-list h4::before { content: ""; width: 11px; height: 11px; background: var(--swatch); }
  .legend-list p { padding-left: 4px; }

  /* Thanks slide */
  .thanks-title {
    position: absolute; left: 220px; top: 112px;
    font-size: 50px; font-weight: 700; color: #000; letter-spacing: -0.5px;
  }
  .thanks-presenter { position: absolute; left: 272px; top: 182px; font-size: 18px; color: var(--ink); }
  .thanks-brand {
    position: absolute; left: 352px; top: 216px;
    color: var(--brand-red); font-weight: 700; font-size: 14px; letter-spacing: 2px; line-height: 1.1;
  }
  .thanks-brand span { display: block; font-size: 10px; letter-spacing: 5px; }
</style>
</head>
<body>

<svg width="0" height="0" style="position:absolute">
  <defs>
    <linearGradient id="band-top" x1="0" x2="1" y1="0" y2="0">
      <stop offset="0" stop-color="#cfcfd2"/>
      <stop offset="1" stop-color="#f7f7f8"/>
    </linearGradient>
    <linearGradient id="band-bottom" x1="0" x2="1" y1="0" y2="0">
      <stop offset="0" stop-color="#f4f4f5"/>
      <stop offset="1" stop-color="#c4c4c7"/>
    </linearGradient>
    <g id="chrome-shapes">
      <path d="M0 0H557V46H385L350 18H0Z" fill="url(#band-top)"/>
      <polyline points="0,18 350,18 385,46 557,46" fill="none" stroke="#d3826a" stroke-width="1.2"/>
      <path d="M0 372H292L334 421H0Z" fill="url(#band-bottom)"/>
      <polyline points="0,372 292,372 334,421" fill="none" stroke="#d3826a" stroke-width="1.2"/>
    </g>
  </defs>
</svg>

<!-- Title slide -->
<section class="slide slide--title">
  <svg class="chrome" viewBox="0 0 557 417" preserveAspectRatio="none"><use href="#chrome-shapes"/></svg>
  <div class="brand-mark"><span class="brand-mark__square"></span>Corvin Ridge<br>Software</div>
  <div class="hero-square"></div>
  <div class="hero-brand">CORVIN RIDGE<span>SOFTWARE</span></div>
  <p class="tagline">Discover the edge. Optimize the whole.</p>
  <h1 class="deck-title">Title of presentation</h1>
  <p class="deck-desc">Description here</p>
  <p class="footer-url">www.YOURWEBID.com</p>
</section>

<!-- Section slide -->
<section class="slide slide--section">
  <svg class="chrome" viewBox="0 0 557 417" preserveAspectRatio="none"><use href="#chrome-shapes"/></svg>
  <div class="brand-mark"><span class="brand-mark__square"></span>Corvin Ridge<br>Software</div>
  <h2 class="page-heading">SECTION TITLE <strong>COMES HERE</strong></h2>
  <p class="page-subheading">Followed by some sub titles here</p>
  <p class="lead">Ask the basic questions as you define and allocate tasks (workload / complexity Dependencies, time to complete, fit with capabilities). Make sure the workload is balanced and allocated fairly Ask the basic questions as you define and allocate task</p>
  <ul class="checklist checklist--left">
    <li><h4>Ask the basic</h4><p>questions as you define and allocate (workload/complexity, dependencies, time to complete, fit with capabilities). Make sure the workload is</p></li>
    <li><h4>Ask the basic</h4><p>questions as you define and allocate (workload/complexity, dependencies, time to complete, fit with capabilities). Make sure the workload is</p></li>
    <li><h4>Ask the basic</h4><p>questions as you define and allocate (workload/complexity, dependencies, time to complete, fit with capabilities). Make sure the workload is</p></li>
  </ul>
  <ul class="checklist checklist--right">
    <li><h4>Ask the basic</h4><p>questions as you define and allocate (workload/complexity, dependencies, capabilities). Make sure the workload is</p></li>
    <li><h4>Ask the basic</h4><p>questions as you define and allocate (workload/complexity, dependencies, capabilities). Make sure the workload is</p></li>
  </ul>
  <svg class="icon-ring" viewBox="0 0 177 200">
    <g fill="#fff" stroke="#d3826a" stroke-width="1.4">
      <circle cx="51" cy="47" r="27"/>
      <circle cx="120" cy="35" r="27"/>
      <circle cx="36" cy="121" r="27"/>
      <circle cx="149" cy="115" r="27"/>
      <circle cx="91" cy="166" r="27"/>
    </g>
    <g fill="#111">
      <ellipse cx="49" cy="38" rx="11" ry="4"/>
      <rect x="38" y="41" width="22" height="6" rx="2"/>
      <rect x="38" y="49" width="22" height="6" rx="2"/>
      <circle cx="61" cy="55" r="6" fill="#fff" stroke="#111" stroke-width="2"/>
      <rect x="107" y="24" width="24" height="6"/>
      <rect x="107" y="32" width="24" height="6"/>
      <rect x="107" y="40" width="18" height="6"/>
      <circle cx="131" cy="45" r="4"/>
      <path d="M26 108h14l5 5v18H26Z"/>
      <rect x="36" y="124" width="9" height="7" fill="#fff" stroke="#111"/>
      <path d="M139 102h14l5 5v18h-19Z"/>
      <rect x="149" y="118" width="9" height="7" fill="#fff" stroke="#111"/>
      <rect x="78" y="155" width="24" height="6"/>
      <rect x="78" y="163" width="24" height="6"/>
      <rect x="78" y="171" width="18" height="6"/>
      <circle cx="102" cy="176" r="4"/>
    </g>
    <rect x="83" y="70" width="16" height="56" rx="5" fill="#d3826a" role="img" aria-label="Figure of a network user at the centre of the icon group"/>
  </svg>
  <p class="footer-url">www.YOURWEBID.com</p>
</section>

<!-- General info slide -->
<section class="slide slide--info">
  <svg class="chrome" viewBox="0 0 557 421" preserveAspectRatio="none"><use href="#chrome-shapes"/></svg>
  <div class="brand-mark"><span class="brand-mark__square"></span>Corvin Ridge<br>Software</div>
  <h2 class="page-heading">GENERALINFO <strong>COMES HERE</strong></h2>
  <p class="page-subheading">Followed by some sub titles here</p>
  <svg class="chart" viewBox="0 0 260 130" font-family="Open Sans, Arial, sans-serif" font-size="8">
    <g stroke="#d9d9d9" stroke-width="0.6">
      <line x1="20" x2="258" y1="6" y2="6"/><line x1="20" x2="258" y1="23" y2="23"/>
      <line x1="20" x2="258" y1="40" y2="40"/><line x1="20" x2="258" y1="57" y2="57"/>
      <line x1="20" x2="258" y1="74" y2="74"/><line x1="20" x2="258" y1="91" y2="91"/>
      <line x1="20" x2="258" y1="108" y2="108" stroke="#999"/>
    </g>
    <g fill="#333" text-anchor="end">
      <text x="13" y="9">6</text><text x="13" y="26">5</text><text x="13" y="43">4</text>
      <text x="13" y="60">3</text><text x="13" y="77">2</text><text x="13" y="94">1</text><text x="13" y="111">0</text>
    </g>
    <g>
      <rect x="28" y="35" width="9" height="73" fill="#8b1d1f"/><rect x="39" y="67" width="9" height="41" fill="#d3826a"/><rect x="50" y="74" width="9" height="34" fill="#e6e6ea"/><rect x="61" y="35" width="9" height="73" fill="#e9b422"/>
      <rect x="84" y="66" width="9" height="42" fill="#8b1d1f"/><rect x="95" y="33" width="9" height="75" fill="#d3826a"/><rect x="106" y="74" width="9" height="34" fill="#e6e6ea"/><rect x="117" y="66" width="9" height="42" fill="#e9b422"/>
      <rect x="140" y="48" width="9" height="60" fill="#8b1d1f"/><rect x="151" y="77" width="9" height="31" fill="#d3826a"/><rect x="162" y="57" width="9" height="51" fill="#e6e6ea"/><rect x="173" y="48" width="9" height="60" fill="#e9b422"/>
      <rect x="196" y="31" width="9" height="77" fill="#8b1d1f"/><rect x="207" y="60" width="9" height="48" fill="#d3826a"/><rect x="218" y="23" width="9" height="85" fill="#e6e6ea"/><rect x="229" y="31" width="9" height="77" fill="#e9b422"/>
    </g>
    <g fill="#222" text-anchor="middle">
      <text x="49" y="124">Category 1</text><text x="105" y="124">Category 2</text>
      <text x="161" y="124">Category 3</text><text x="217" y="124">Category 4</text>
    </g>
  </svg>
  <p class="chart-heading"><strong>YOUR CHART HERADING COMES HERE:</strong>&emsp;&emsp;&emsp;&emsp;&ensp;Ask the basic questions as you define and allocate tasks (workload / DFGSFD complexity Dependencies, time to complete, fit with capabilities). Make sure the workload is balanced and allocated fairly Ask the basic questions as you define and allocate task</p>
  <ul class="legend-list">
    <li style="--swatch: var(--brand-red)"><h4>Ask the basic</h4><p>questions as you define and allocate (workload/complexity, dependencies, time to complete, fit with capabilities). Make sure the workload is</p></li>
    <li style="--swatch: var(--brand-copper)"><h4>Ask the basic</h4><p>questions as you define and allocate (workload/complexity, dependencies, time to complete, fit with capabilities). Make sure the workload is</p></li>
    <li style="--swatch: var(--mist)"><h4>Ask the basic</h4><p>questions as you define and allocate (workload/complexity, dependencies, time to complete, fit with capabilities). Make sure the workload is</p></li>
    <li style="--swatch: var(--brand-gold)"><h4>Ask the basic</h4><p>questions as you define and allocate (workload/complexity, dependencies, time to complete, fit with capabilities). Make sure the workload is</p></li>
  </ul>
  <p class="footer-url">www.YOURWEBID.com</p>
</section>

<!-- Thank you slide -->
<section class="slide slide--thanks">
  <svg class="chrome" viewBox="0 0 557 421" preserveAspectRatio="none"><use href="#chrome-shapes"/></svg>
  <div class="brand-mark"><span class="brand-mark__square"></span>Corvin Ridge<br>Software</div>
  <h2 class="thanks-title">Thank you</h2>
  <p class="thanks-presenter">Name of the presenter</p>
  <div class="thanks-brand">CORVIN RIDGE<span>SOFTWARE</span></div>
  <p class="footer-url">www.YOURWEBID.com</p>
</section>

</body>
</html>
```